Real Estate agent needs flyer/folder to contain bio and overview of services

I'm including files of the layout of the small folder. The folder is 6 1/2 across and 9 1/2 inches long. It will have a front & back cover and then writing on the 2 inside pages.

I am sending a few files to incorporate into the flyer, 1 new logo to use and 2 files which are coloring ideas.

Colors

Designer to choose colors to be used in the design.

```html
<!DOCTYPE html>
<html lang="en">
<head>
<meta charset="utf-8">
<title>Marla Venturi – Realtor Folder</title>
<link rel="stylesheet" href="https://fonts.googleapis.com/css2?family=Arvo:wght@700&family=Libre+Baskerville:ital,wght@0,400;0,700;1,400&family=Tinos:ital,wght@0,400;0,700;1,400&family=Open+Sans:wght@400;600&display=swap">
<style>
  :root{
    --brand-blue:#2f5fb3;
    --deep-blue:#1f4597;
    --ink:#3a3a3a;
    --soft-ink:#555555;
    --paper:#ffffff;
    --stage:#ececee;
  }
  *{margin:0;padding:0;box-sizing:border-box}
  html,body{width:837px;height:1200px;overflow:hidden;background:var(--stage)}
  .canvas{position:relative;width:837px;height:1200px}
  .shapes{position:absolute;inset:0}
  .abs{position:absolute}

  .brokerage{left:70px;top:140px;font-family:"Libre Baskerville",serif;font-weight:700;font-size:10px;color:var(--brand-blue);letter-spacing:.5px;line-height:1.25;display:flex;align-items:center;gap:5px}
  .brokerage .dot{width:9px;height:9px;border-radius:50%;background:var(--brand-blue)}
  .agent-mark{font-family:"Libre Baskerville",serif;font-weight:400;color:var(--brand-blue);white-space:nowrap}
  .agent-mark.small{left:160px;top:140px;font-size:24px}
  .agent-mark.large{left:440px;top:350px;width:310px;text-align:center;font-size:30px}

  .cover-intro{left:77px;top:245px;width:160px;font-family:"Tinos",serif;font-weight:700;font-size:6.6px;line-height:1.38;color:var(--ink)}
  .agent-card{left:206px;top:428px;font-family:"Open Sans",sans-serif;color:var(--ink)}
  .agent-card .name{font-size:9px}
  .agent-card .role{font-size:8px}
  .agent-card .license{font-size:6px;margin-bottom:4px}
  .agent-card .welcome{font-family:"Tinos",serif;font-style:italic;font-size:9px;line-height:1.25}

  .contact{left:78px;top:514px;font-family:"Open Sans",sans-serif;color:#fff}
  .contact .name{font-size:11px;margin-bottom:4px}
  .contact .line{display:flex;align-items:center;gap:6px;font-size:8.3px;height:13.5px}
  .contact svg{width:10px;height:10px}

  .news{left:440px;top:498px;font-family:"Libre Baskerville",serif;font-weight:700;font-size:27px;line-height:31px;color:var(--soft-ink)}

  .col{font-family:"Tinos",serif;font-size:6.4px;line-height:9.3px;color:var(--ink);text-align:justify}
  .col p{margin-bottom:9px}
  .col h2{font-family:"Arvo",serif;font-weight:700;font-size:13.5px;line-height:19px;color:var(--brand-blue);letter-spacing:.5px;text-align:left;margin-bottom:7px}
  .col h2.gap{margin-top:8px}
  .col-intro{left:245px;top:640px;width:152px}
  .col-selling{left:449px;top:640px;width:140px}
  .col-buying{left:613px;top:640px;width:138px}

  .testimonials{left:418px;top:918px;width:363px;height:226px;padding:14px 36px 0;text-align:center;color:#fff;font-family:"Tinos",serif}
  .testimonials h3{font-family:"Libre Baskerville",serif;font-weight:700;font-size:13px;letter-spacing:.5px;margin-bottom:7px}
  .testimonials p{font-size:6.3px;line-height:9.2px}
  .testimonials .by{font-weight:700;font-size:7.6px;margin:2px 0 8px}
</style>
</head>
<body>
<div class="canvas">
  <svg class="shapes" viewBox="0 0 837 1200" width="837" height="1200">
    <defs>
      <clipPath id="right-cover-cut"><path d="M418,56 L696,56 C760,140 772,420 688,586 L418,586 Z"/></clipPath>
      <clipPath id="inside-cut"><path d="M128,614 L781,614 L781,1144 L132,1144 C80,1060 60,720 128,614 Z"/></clipPath>
      <linearGradient id="g-front" x1="0" y1="0" x2="1" y2="1">
        <stop offset="0" stop-color="#c9d3e0"/><stop offset=".55" stop-color="#b9b3ab"/><stop offset="1" stop-color="#d9dde4"/>
      </linearGradient>
      <linearGradient id="g-night" x1="0" y1="0" x2="1" y2="1">
        <stop offset="0" stop-color="#26344f"/><stop offset=".5" stop-color="#8a6a46"/><stop offset="1" stop-color="#3d83b8"/>
      </linearGradient>
      <linearGradient id="g-villa" x1="0" y1="0" x2="0" y2="1">
        <stop offset="0" stop-color="#6f9fd6"/><stop offset=".45" stop-color="#e6dccb"/><stop offset=".75" stop-color="#8e8a6e"/><stop offset="1" stop-color="#6fa8b8"/>
      </linearGradient>
      <linearGradient id="g-fade" x1="0" y1="0" x2="1" y2="0">
        <stop offset="0" stop-color="#fff" stop-opacity="0"/><stop offset="1" stop-color="#fff" stop-opacity=".75"/>
      </linearGradient>
    </defs>

    <!-- front cover -->
    <rect x="56" y="56" width="362" height="530" fill="var(--paper)"/>
    <polygon role="img" aria-label="Photo of the agent in front of a modern home with pool" points="56,212 418,232 418,484 204,524 56,512" fill="url(#g-front)"/>
    <polygon points="200,420 418,410 418,484 204,524" fill="url(#g-fade)"/>
    <polygon points="344,222 418,218 418,256" fill="var(--deep-blue)"/>
    <polygon points="56,500 204,524 418,480 418,586 56,586" fill="var(--brand-blue)"/>
    <polygon points="230,520 418,480 418,586 300,586" fill="var(--deep-blue)" opacity=".55"/>
    <rect x="342" y="526" width="20" height="24" fill="none" stroke="#9fb6dd" stroke-width="1.2"/>
    <rect x="374" y="526" width="26" height="24" fill="none" stroke="#9fb6dd" stroke-width="1.2"/>

    <!-- back cover -->
    <g clip-path="url(#right-cover-cut)">
      <rect x="418" y="56" width="360" height="530" fill="var(--paper)"/>
      <polygon role="img" aria-label="Photo of a luxury home and pool at dusk" points="418,56 780,56 780,185 418,172" fill="url(#g-night)"/>
      <polygon points="540,178 780,186 780,240" fill="var(--deep-blue)"/>
    </g>
    <path d="M418,56 L696,56 C760,140 772,420 688,586 L418,586" fill="none" stroke="#333" stroke-width="1"/>

    <!-- inside spread -->
    <g clip-path="url(#inside-cut)">
      <rect x="60" y="614" width="730" height="530" fill="var(--paper)"/>
      <rect role="img" aria-label="Photo of a Mediterranean-style community entrance with fountain" x="60" y="614" width="178" height="530" fill="url(#g-villa)"/>
      <rect x="418" y="918" width="363" height="226" fill="var(--brand-blue)"/>
    </g>
  </svg>

  <!-- front cover -->
  <div class="abs brokerage"><span class="dot"></span><span>SUMMIT<br>REALTY</span></div>
  <div class="abs agent-mark small">Marla Venturi</div>
  <div class="abs cover-intro">Along with being your Realtor, I'm a lifelong resource for all things home-related &amp; beyond... if you need a great referral for anything at all, call me! I can't wait to work with you!</div>
  <div class="abs agent-card">
    <div class="name">Marla Venturi</div>
    <div class="role">Realtor ®</div>
    <div class="license">DRE# 02145587</div>
    <div class="welcome">Please feel welcome to call me<br>for all things home related.<br>I will look forward to meeting you!</div>
  </div>
  <div class="abs contact">
    <div class="name">MARLA VENTURI</div>
    <div class="line"><svg viewBox="0 0 10 10"><circle cx="5" cy="5" r="4.5" fill="none" stroke="#fff" stroke-width=".8"/><path d="M3.3,2.8 L4.2,2.6 L4.6,3.8 L4,4.3 Q4.6,5.5 5.7,6 L6.2,5.4 L7.4,5.8 L7.2,6.7 Q4.2,6.9 3.3,2.8Z" fill="#fff"/></svg>555 014 2290</div>
    <div class="line"><svg viewBox="0 0 10 10"><circle cx="5" cy="5" r="4.5" fill="none" stroke="#fff" stroke-width=".8"/><rect x="2.8" y="3.4" width="4.4" height="3.2" fill="#fff"/><path d="M2.8,3.4 L5,5.2 L7.2,3.4" fill="none" stroke="var(--brand-blue)" stroke-width=".5"/></svg>marla@venturihomes.com</div>
    <div class="line"><svg viewBox="0 0 10 10"><circle cx="5" cy="5" r="4.5" fill="none" stroke="#fff" stroke-width=".8"/><circle cx="5" cy="5" r="2.6" fill="none" stroke="#fff" stroke-width=".6"/><path d="M2.4,5 H7.6 M5,2.4 V7.6" stroke="#fff" stroke-width=".5"/></svg>www.venturihomes.com</div>
  </div>

  <!-- back cover -->
  <div class="abs agent-mark large">Marla Venturi</div>
  <div class="abs news">We've Got<br>News For You...</div>

  <!-- inside -->
  <div class="abs col col-intro">
    <h2>LET ME INTRODUCE MYSELF</h2>
    <p>I'm originally from Chicago, but I'm a full-fledged California girl now. I've lived and worked in Orange County since 1996. I always say where we live is the next best thing to living on a tropical island. I've traveled to many and I'm always happy to come back to my Laguna Niguel home.</p>
    <p>My passion for this area is why I'm in Real Estate. I consider myself incredibly fortunate to sell homes and help people purchase homes in an area that I love with all my heart.</p>
    <p>This passion also carries over in representing my clients with the highest degree of professionalism, enthusiasm and care. My business is built on exceptional customer service and I'm grateful my clients are mostly repeat and referrals.</p>
    <h2 class="gap">MY CORE TENET</h2>
    <p>It's All About YOU!<br>My #1 priority is understanding YOUR needs and YOUR objectives. This understanding, along with working diligently on your behalf, means we accomplish your goal whether you're purchasing your 1st home or selling a home you've loved so you can move on to the next chapter of your life</p>
    <h2 class="gap">REAL ESTATE SERVICES &amp; BEYOND...</h2>
    <p>Simply put, I help people who are local, relocating and investing, sell and purchase homes in Southern California. For purchases outside of California, I can refer to a network of agents across the country.<br>I also provide a team who is dedicated to providing outstanding customer service throughout the transaction. My team includes a network of lenders, title, and escrow officers, in house CPA, stagers, photographers, contractors and more.</p>
  </div>

  <div class="abs col col-selling">
    <h2>SELLING YOUR HOME</h2>
    <p>Selling your home is not like any other business transaction. It's also personal. My priority as your Listing Agent is to guide you through what can be a complicated and sometimes emotional process.</p>
    <p>I place great emphasis on marketing your property with professional photographs, along with harnessing the power of the Internet and the virtual world to reach as many buyers as possible. Your property will be marketed to the public as well as to other agents, thus creating maximum exposure of your home.</p>
    <p>When we first meet to discuss selling your home, it's essential for me to gain an understanding of your unique needs such as timelines, expectations and financial considerations, just to name a few. From there, I begin the process of listing and marketing your home. I lead you through negotiations and more paperwork than you ever care to do, guiding you to the successful closing of your home.</p>
  </div>

  <div class="abs col col-buying">
    <h2>BUYING A HOME</h2>
    <p>If you're thinking about buying a home, it's imperative you have an accomplished, real estate professional by your side to walk you through what is likely the largest purchase of your life.</p>
    <p>To get started, I like to meet with you so we have an opportunity to get to know each other as purchasing a home is a uniquely, personal endeavor. At that time, we can discuss your goals and if it's a good time for you to purchase a home.</p>
    <p>From there, the first step is to obtain a pre-approval from a lender. I'm able to recommend various lenders who can introduce and explain the various loan products available.</p>
    <p>After you've been pre-approved, that's when the fun starts! I guide you through the home buying adventure every step of the way and look forward to handing you the keys to your new home.</p>
  </div>

  <div class="abs testimonials">
    <h3>TESTIMONIALS:</h3>
    <p>Marla got us an amazing deal on our new home and sold our old home in a week. Marla is patient, hardworking, professional and most importantly HONEST. Marla is definitely one of the best in the business!</p>
    <p class="by">Dana &amp; Aaron Holt</p>
    <p>Marla is the kind of Real Estate professional everyone wants to represent them. She is knowledgeable, ethical, energetic, and follows up on every detail. Her honesty, integrity and expertise combined make her a very special and remarkable professional. We were lucky to find her!</p>
    <p class="by">Henry &amp; Claire Moss</p>
    <p>During the home buying process, Marla becomes your trusted advisor, mentor and friend. Her knowledge of the industry, community and market are best in class. A true professional! Marla aligned her goals with my own and understood the motivation behind my purchase. Marla is unequivocally the reason why I was able to purchase my home in Laguna Niguel and provide my family with a world-class community. Without her guidance and experience, I would still be in the market attempting to navigate the ever-changing work of real estate.</p>
    <p class="by">Rafael Ortega</p>
  </div>
</div>
</body>
</html>
```